New Graphic Design Project / Email signiture and Letterhead

I would like a new SIMPLE but high end quality modern/heavy industrial design for an email Signiture and letter head that incorporates product photos or illustrations of our products to show our customers our range of products and also show our head office in Perth Western Australia and also our Australian and international reseller locations.
in my present email signature you would see that I have other company logos these companies are old partners of ours but some are no longer so I would like to have the option to add and change them if things change in the future.
for ideas Our main products are as follows
Composite Hose
Convoluted hose
Metal expansion joints
Fabric expansion joints
Rubber Expansion joints
Please see our website for ideas and our product photos.
www.norvaquip.com.au
if you need any further information please let me know
i have attached our old email signiture for reference.
Dale

Target Market(s)

Oil and Gas / Mining / Petroleum and Chemical Refineries, high end engineering

Requirements
Must have
• pictures / photos of our core products and our company capabilities to show our existing and new customers what we can do.
in the email signature - links to company face book and LinkedIn, our website
I would like to have spaces for my company partners logos and need the final file to be in a format for me to change and update all details
All so our Font is Conthrax SB
Nice to have
• the email signature, I would like this to have all the required information ( as per attached present email signature ) but also be informative / marketing to show customers what we do if possible.
the letter head can be based from the same but simple with or without product photos

```html
<!DOCTYPE html>
<html lang="en">
<head>
<meta charset="utf-8">
<title>Norvaquip Letterhead</title>
<link rel="stylesheet" href="https://fonts.googleapis.com/css2?family=Lato:wght@400;700;900&display=swap">
<style>
  :root {
    --backdrop: #e4e4e4;
    --paper: #ffffff;
    --ink: #111111;
    --ink-soft: #6b6b6b;
    --mark: #555555;
    --band-grey: #5a5a5a;
    --band-dark: #0d0d0d;
    --badge-1: #d43a3a;
    --badge-2: #9a7c5c;
    --badge-3: #3f8f9a;
    --badge-4: #1e3f8c;
    --badge-5: #2e4f96;
    --badge-6: #13224d;
    --badge-7: #8a8a8a;
    --badge-8: #c9a23b;
  }
  * { box-sizing: border-box; margin: 0; padding: 0; }
  html, body {
    width: 1056px; height: 1200px; overflow: hidden;
    background: var(--backdrop);
    font-family: "Lato", Arial, sans-serif;
  }
  .letterhead {
    position: absolute; left: 108px; top: 6px;
    width: 840px; height: 1188px;
    background: var(--paper);
  }
  .brand {
    position: absolute; left: 77px; top: 79px;
    display: flex; align-items: center; gap: 14px;
  }
  .brand-dot {
    width: 70px; height: 70px; border-radius: 50%;
    border: 7px solid var(--mark);
  }
  .brand-name {
    font-weight: 900; font-size: 34px; letter-spacing: 2px;
    color: var(--ink);
  }
  .contact {
    position: absolute; left: 617px; top: 60px; width: 210px;
    font-size: 13.5px; line-height: 17px; color: var(--ink-soft);
  }
  .contact strong { color: var(--ink); font-weight: 700; }
  .contact p { margin-bottom: 3px; }
  .contact-lines { list-style: none; margin-top: 6px; }
  .contact-lines li {
    display: flex; align-items: center; gap: 14px; height: 19px;
  }
  .contact-lines svg { width: 14px; height: 14px; fill: var(--ink); }
  .partners {
    position: absolute; left: 28px; top: 1125px;
    display: flex; align-items: center; gap: 24px;
  }
  .partner { height: 22px; border-radius: 2px; }
  .partner.round { width: 28px; height: 28px; border-radius: 50%; }
  .footer-bands { position: absolute; left: 0; bottom: 0; width: 840px; height: 32px; }
  .web {
    position: absolute; right: 28px; bottom: 7px;
    font-size: 14px; color: #ffffff; letter-spacing: 0.3px;
  }
</style>
</head>
<body>
  <main class="letterhead">
    <header class="brand">
      <span class="brand-dot"></span>
      <span class="brand-name">NORVAQUIP</span>
    </header>

    <address class="contact" style="font-style:normal">
      <p><strong>Head Office:</strong> 212 Tanner Road Kenwick, WA 6107</p>
      <p><strong>Locations:</strong> Australia, Singapore, Indonesia, Vietnam</p>
      <ul class="contact-lines">
        <li>
          <svg viewBox="0 0 24 24" aria-hidden="true"><path d="M6.6 10.8a15 15 0 0 0 6.6 6.6l2.2-2.2a1 1 0 0 1 1-.25 11.4 11.4 0 0 0 3.6.57 1 1 0 0 1 1 1V20a1 1 0 0 1-1 1A17 17 0 0 1 3 4a1 1 0 0 1 1-1h3.5a1 1 0 0 1 1 1c0 1.25.2 2.45.57 3.57a1 1 0 0 1-.25 1z"/></svg>
          <span>+614 00 555 218</span>
        </li>
        <li>
          <svg viewBox="0 0 24 24" aria-hidden="true"><path d="M6 2h12v5H6zM3 8h18a1 1 0 0 1 1 1v7h-4v6H6v-6H2V9a1 1 0 0 1 1-1zm5 8v4h8v-4z"/></svg>
          <span>+614 00 555 947</span>
        </li>
        <li>
          <svg viewBox="0 0 24 24" aria-hidden="true"><path d="M2 5h20v14H2zm2 2v.4l8 5.6 8-5.6V7zm0 2.8V17h16V9.8l-8 5.6z"/></svg>
          <span>dale@norvaquip.com.au</span>
        </li>
      </ul>
    </address>

    <div class="partners" aria-label="Partner and certification badges">
      <span class="partner" style="width:110px;background:var(--badge-1)"></span>
      <span class="partner" style="width:66px;background:var(--badge-2)"></span>
      <span class="partner round" style="background:var(--badge-3)"></span>
      <span class="partner" style="width:34px;background:var(--badge-4)"></span>
      <span class="partner" style="width:38px;background:var(--badge-5)"></span>
      <span class="partner" style="width:48px;background:var(--badge-6)"></span>
      <span class="partner round" style="background:var(--badge-7)"></span>
      <span class="partner" style="width:84px;background:var(--badge-8)"></span>
    </div>

    <svg class="footer-bands" viewBox="0 0 840 32" aria-hidden="true">
      <polygon points="0,6 208,6 203,12 0,12" fill="var(--band-grey)"/>
      <polygon points="212,6 430,6 423,12 205,12" fill="var(--band-dark)"/>
      <polygon points="434,6 645,6 640,12 427,12" fill="var(--band-grey)"/>
      <polygon points="0,17 636,17 658,0 840,0 840,32 0,32" fill="var(--band-dark)"/>
    </svg>
    <span class="web">www.norvaquip.com.au</span>
  </main>
</body>
</html>
```